"Beyond The Grey Harbor" Fictional Book Cover

BEYOND THE GREY HARBOR
By: Derek Falloway

Here's the intro .

"It had been nearly forty years since Tim Ashworth last went to the island from where he was raised. Three months earlier he never would have thought about ever coming back. But life is weird. Things happen quickly and plans change, especially when your very life is at stake. The reason he was going back wasn’t to see old friends...no, no, no. They’re all dead. Of all the kids he grew up with on the island who moved off, he’s the only one still alive. Why?"

Pretty much all just a Lumora book, by the way.

Target Market(s)

fiction readers

Requirements
Must have
• Somewhat of a dark, mysterious cover is what I'd like to see. Use your imagination. I've never written a fiction book before so I'm very open to ideas

Needs to have my name, DEREK FALLOWAY at the bottom. like my other books, all of which are non-fiction
Nice to have
• Mysterious is what I'm looking for. NOT A HORROR story though. More a guy who left the island years ago, but is being called back to escape the rat race of modern, consumerist culture.

Please remember this NEEDS to jump out as a thumbnail on Brevix as people are browsing. Mainly the WORDS need to stick out. Lighter words on a say a blue background.

If you want to try to use the attached pic, or something like this, to reflect an island in the cover, that'd be good.

I've also uploaded a couple images I purchased from Pictoravault, hopefully you can make something work with these.

```html
<!DOCTYPE html>
<html lang="en">
<head>
<meta charset="utf-8">
<title>Beyond The Grey Harbor — Derek Falloway</title>
<link rel="stylesheet" href="https://fonts.googleapis.com/css2?family=Great+Vibes&family=Cinzel:wght@400&family=Open+Sans:wght@400&display=swap">
<style>
  :root {
    --sky-top: #262c7e;
    --sky-indigo: #3d3a9a;
    --sky-violet: #6a46a8;
    --sky-mauve: #a9559f;
    --sky-pink: #dc6a92;
    --sky-coral: #ec9273;
    --sky-glow: #fbe6b0;
    --shore-light: #c9a774;
    --shore-green: #1c3323;
    --shore-dark: #161a1c;
    --pier-shadow: #1b1d2a;
    --water-mid: #1e2850;
    --water-deep: #0c1128;
    --title-ink: #ffffff;
    --title-shadow: rgba(30, 12, 50, 0.8);
  }
  html, body {
    margin: 0;
    padding: 0;
    width: 840px;
    height: 1200px;
    overflow: hidden;
    background: var(--water-deep);
  }
  .cover {
    position: relative;
    width: 840px;
    height: 1200px;
    overflow: hidden;
  }
  .cover-scene {
    position: absolute;
    inset: 0;
  }
  .scene-sky {
    position: absolute;
    left: 0;
    top: 0;
    width: 840px;
    height: 820px;
    background:
      radial-gradient(ellipse 320px 70px at 52% 700px, rgba(255, 247, 220, 0.95), rgba(255, 236, 190, 0) 100%),
      radial-gradient(ellipse 520px 220px at 70% 40px, rgba(20, 18, 60, 0.55), rgba(20, 18, 60, 0) 100%),
      linear-gradient(to bottom,
        var(--sky-top) 0px,
        var(--sky-indigo) 120px,
        var(--sky-violet) 260px,
        var(--sky-mauve) 420px,
        var(--sky-pink) 540px,
        var(--sky-coral) 640px,
        var(--sky-glow) 730px,
        var(--shore-light) 820px);
  }
  .scene-shore {
    position: absolute;
    left: 0;
    top: 790px;
    width: 840px;
    height: 170px;
    background:
      radial-gradient(ellipse 260px 60px at 50% 150px, rgba(190, 150, 120, 0.35), rgba(0, 0, 0, 0) 100%),
      linear-gradient(to bottom,
        rgba(28, 51, 35, 0) 0px,
        var(--shore-green) 30px,
        var(--shore-dark) 110px,
        var(--pier-shadow) 170px);
  }
  .scene-water {
    position: absolute;
    left: 0;
    top: 950px;
    width: 840px;
    height: 250px;
    background:
      radial-gradient(ellipse 300px 40px at 50% 10px, rgba(60, 70, 120, 0.5), rgba(0, 0, 0, 0) 100%),
      linear-gradient(to bottom,
        var(--water-mid) 0px,
        #17203f 90px,
        var(--water-deep) 250px);
  }
  .title {
    position: absolute;
    left: 0;
    right: 0;
    top: 168px;
    margin: 0;
    text-align: center;
    color: var(--title-ink);
    font-weight: 400;
    text-shadow: 0 0 2px var(--title-shadow), 2px 3px 5px var(--title-shadow);
  }
  .title-lead {
    display: block;
    font-family: "Great Vibes", cursive;
    font-size: 136px;
    line-height: 1;
    margin-left: 20px;
  }
  .title-main {
    display: block;
    font-family: "Cinzel", serif;
    font-size: 100px;
    line-height: 1;
    margin-top: 0px;
    letter-spacing: 0;
  }
  .author {
    position: absolute;
    left: 0;
    right: 0;
    top: 1096px;
    margin: 0;
    text-align: center;
    font-family: "Open Sans", sans-serif;
    font-weight: 400;
    font-size: 44px;
    line-height: 1;
    letter-spacing: 12px;
    color: var(--title-ink);
    text-shadow: 1px 2px 4px rgba(0, 0, 0, 0.6);
  }
</style>
</head>
<body>
  <main class="cover">
    <div class="cover-scene" role="img" aria-label="Photograph of an island ferry pier with waterfront houses and trees under a purple, pink and golden sunset sky, dark harbor water in the foreground">
      <div class="scene-sky"></div>
      <div class="scene-shore"></div>
      <div class="scene-water"></div>
    </div>
    <h1 class="title">
      <span class="title-lead">Beyond the</span>
      <span class="title-main">GREY HARBOR</span>
    </h1>
    <p class="author">DEREK FALLOWAY</p>
  </main>
</body>
</html>
```